Business Card Design & Gift cards, Gift Cert, Donation Card

Retail Gift Store-in addition to Business Cards we'd like sequenced 2 sided Gift cards, Gift Certificate Cards, and Donation Cards.please see examples and email for clarificationlogos attached with examples-
Gift Card, Gift Certificate and Donation Card will all be same style just differant upper right title, with back side info as example.
business card, as example is single sided.
looking for additional ideas for layout

Industry/Entity Type

Business

Contact Information for Business Card

211 Newman St.Harbor Bend, MI 48730989.362.8730Office@BrewKrew.com

Requirements
Must have
• Blue as per example
• Logos provided
• like gradiant background

```html
<!DOCTYPE html>
<html lang="en">
<head>
<meta charset="utf-8">
<title>Tillow Marsh – Business Card</title>
<link rel="stylesheet" href="https://fonts.googleapis.com/css2?family=Marcellus+SC&display=swap">
<style>
  :root {
    --page-bg: #e9e6e1;
    --brand-blue: #3f55c4;
    --brand-blue-deep: #3446ad;
    --sun-yellow: #f2ea2c;
    --ink-white: #ffffff;
    --card-shadow: rgba(40, 30, 20, 0.28);
  }
  * { box-sizing: border-box; margin: 0; padding: 0; }
  html, body {
    width: 1200px; height: 892px; overflow: hidden;
    background: var(--page-bg);
    font-family: "Marcellus SC", "Optima", serif;
  }
  .canvas {
    position: relative; width: 1200px; height: 892px;
    display: flex; justify-content: center; align-items: center; gap: 80px;
  }
  .card {
    position: relative; width: 340px; height: 595px;
    border-radius: 6px; overflow: hidden;
    box-shadow: 0 14px 30px var(--card-shadow);
  }
  .card-surface { position: absolute; inset: 0; width: 100%; height: 100%; }
  .brand-name {
    position: absolute; top: 48px; left: 0; right: 0;
    text-align: center; color: var(--ink-white);
    font-size: 38px; font-weight: 400; letter-spacing: 2px;
  }
  .mark-art {
    position: absolute; left: 60px; width: 220px; height: 220px;
    border-radius: 10px;
    background: linear-gradient(180deg, var(--brand-blue) 0%, var(--brand-blue) 62%, var(--sun-yellow) 100%);
    opacity: 0.9;
  }
  .card-front .mark-art { top: 140px; }
  .card-back .mark-art { top: 200px; }
  .contact {
    position: absolute; left: 0; right: 0; bottom: 60px;
    text-align: center; color: var(--ink-white);
    font-style: normal; font-size: 16px; line-height: 1.6; letter-spacing: 1.5px;
  }
</style>
</head>
<body>
<main class="canvas">

  <section class="card card-front" aria-label="Business card front">
    <svg class="card-surface" viewBox="0 0 340 595" preserveAspectRatio="none" aria-hidden="true">
      <defs>
        <linearGradient id="paperFront" x1="0" y1="0" x2="0" y2="1">
          <stop offset="0" stop-color="#cfcfcf"/>
          <stop offset="1" stop-color="#ececec"/>
        </linearGradient>
        <linearGradient id="blueFront" x1="0" y1="0" x2="0" y2="1">
          <stop offset="0" stop-color="#4a5fcc"/>
          <stop offset="1" stop-color="#3446ad"/>
        </linearGradient>
      </defs>
      <rect width="340" height="595" fill="url(#paperFront)"/>
      <path d="M0 300 Q180 420 340 330 L340 595 L0 595 Z" fill="url(#blueFront)"/>
    </svg>
    <h1 class="brand-name">Tillow Marsh</h1>
    <div class="mark-art" role="img" aria-label="Illustration of a running stick figure with wild hair over a rising yellow sun"></div>
    <address class="contact">
      555.517.4296<br>
      Office@TillowMarsh.com<br>
      482 Larkfield Ave. Harbor Bend,<br>
      MI 49215
    </address>
  </section>

  <section class="card card-back" aria-label="Business card back">
    <svg class="card-surface" viewBox="0 0 340 595" preserveAspectRatio="none" aria-hidden="true">
      <defs>
        <linearGradient id="paperBack" x1="0" y1="0" x2="0" y2="1">
          <stop offset="0" stop-color="#d4d4d4"/>
          <stop offset="1" stop-color="#eeeeee"/>
        </linearGradient>
        <linearGradient id="blueBack" x1="0" y1="0" x2="0" y2="1">
          <stop offset="0" stop-color="#4a5fcc"/>
          <stop offset="1" stop-color="#3446ad"/>
        </linearGradient>
      </defs>
      <rect width="340" height="595" fill="url(#paperBack)"/>
      <path d="M0 330 Q200 410 340 150 L340 595 L0 595 Z" fill="url(#blueBack)"/>
    </svg>
    <div class="mark-art" role="img" aria-label="Illustration of a running stick figure with wild hair over a rising yellow sun"></div>
  </section>

</main>
</body>
</html>
```